Project Lists Banner for HVAC ecommerce store

We want a banner that showcases our project list feature that will allow customers to create list of products that they can select and quickly order. this will be a middle of page banner. It will replace this banner - https://www.lumapixvault.com/image/84730295
Font: Noto Sans
Size: 938x300 px
Color Options: #0059E, #00BBE3, #C6C8C7
Text:
Create lists of frequently purchased SKU's for fast ordering.
- Warehouse Inventory
- Complete Systems
- Large Projects
- And More...
"Sign In" is the call to action button. make button with non rounded (square) boarders.
We don't want a computer screen in banner nor a person. You can look at our competitors below for ideas.
Our staging server is belfarq7.com for reference
Our competitors:
https://www.brantlowholdings.com/
https://www.folvexa.com/
https://www.zelbrk.com/
https://www.vostrel.com/index.html
HVAC, B2B
HVAC

```html
<!DOCTYPE html>
<html lang="en">
<head>
<meta charset="UTF-8">
<title>Project Lists Banner</title>
<link rel="stylesheet" href="https://fonts.googleapis.com/css2?family=Noto+Sans:ital,wght@0,400;0,700;1,300;1,400;1,700&display=swap">
<style>
  :root {
    --brand-navy: #00059e;
    --brand-cyan: #00bbe3;
    --brand-silver: #c6c8c7;
    --brand-white: #ffffff;
    --stage-black: #000000;
  }
  * { margin: 0; padding: 0; box-sizing: border-box; }
  html, body {
    width: 1200px;
    height: 657px;
    overflow: hidden;
    background: var(--stage-black);
    font-family: "Noto Sans", sans-serif;
  }
  .banner {
    position: absolute;
    left: 151px;
    top: 185px;
    width: 938px;
    height: 300px;
    transform: scale(0.957);
    transform-origin: 0 0;
    overflow: hidden;
    background: linear-gradient(to bottom, var(--brand-white) 0%, var(--brand-silver) 40%, var(--brand-silver) 100%);
  }
  .banner__shapes {
    position: absolute;
    inset: 0;
  }
  .headline {
    position: absolute;
    left: 52px;
    top: 58px;
    color: var(--brand-white);
    font-style: italic;
    text-transform: uppercase;
  }
  .headline__line {
    display: block;
    font-weight: 400;
    font-size: 37px;
    line-height: 45px;
    letter-spacing: -0.3px;
  }
  .headline__line--emphasis {
    font-size: 37px;
    line-height: 54px;
    font-weight: 400;
  }
  .headline__strong {
    font-weight: 700;
    font-size: 44px;
  }
  .headline__line--bold {
    font-weight: 700;
    line-height: 44px;
  }
  .feature-list {
    position: absolute;
    left: 600px;
    top: 66px;
    width: 310px;
    list-style: none;
    text-align: center;
    color: var(--brand-navy);
    font-weight: 700;
    font-size: 22px;
    line-height: 36px;
    text-transform: uppercase;
  }
  .cta-signin {
    position: absolute;
    left: 514px;
    top: 215px;
    width: 155px;
    height: 52px;
    background: var(--brand-cyan);
    color: var(--brand-white);
    font-weight: 700;
    font-size: 22px;
    line-height: 52px;
    text-align: center;
    text-transform: uppercase;
    text-decoration: none;
    border-radius: 0;
  }
</style>
</head>
<body>
  <section class="banner" aria-label="Project lists feature">
    <svg class="banner__shapes" width="938" height="300" viewBox="0 0 938 300" aria-hidden="true">
      <polygon points="0,0 491,0 615,300 0,300" fill="var(--brand-navy)"/>
      <polygon points="491,0 509,0 620,300 615,300" fill="var(--brand-cyan)"/>
    </svg>

    <h2 class="headline">
      <span class="headline__line">Create lists of</span>
      <span class="headline__line">frequently purchased</span>
      <span class="headline__line headline__line--emphasis"><span class="headline__strong">SKU's</span> for</span>
      <span class="headline__line headline__line--bold">fast ordering</span>
    </h2>

    <ul class="feature-list">
      <li>Warehouse Inventory</li>
      <li>Complete Systems</li>
      <li>Large Projects</li>
      <li>And More...</li>
    </ul>

    <a class="cta-signin" href="#">Sign In</a>
  </section>
</body>
</html>
```